Business cards for Norwegian software consultancy business

We are in need of business cards for our Norwegian consultancy company.
“Valto Brindex AS” specializes in software development, architecture and agile methodology, providing mostly on-site services at customers.
The cards should reflect a certain level of business professionalism with an elegant touch, while paying tribute to our modern and technological heritage. Our logo should be featured, as well as room for basic information about the cardholder and legal information of the company (company name, address and VAT number).
We would like our cards to reflect that we are a modern consulting company. It should present a professional image that people will remember. The texture and color pallette should reflect our professionalism and reliability, so we prefer a light color pallette with colors such as gray, white, blue and black. The number of colors used should however not be overwhelming, with the text being distinct and readable.
We are open to untraditional layouts and playful designs as long as they communicate the intent stated above.
You could also take a look at our website http://www.brindex.no for input on our visual profile.
Our logo is attached in the form of vectors and rasterized PNG. Please comment if you would like the black-white and/or inverted versions as well.
Industry/Entity Type
Architecture
Contact Information for Business Card
Company information:
Valto Brindex AS
Kvernlia 14, 3170 Sem
482 71 519
info@brindex.no
www.brindex.no
Employee information:
Full name
Title
Email
Phone
Font styles to use
Look and feel

```html
<!DOCTYPE html>
<html lang="no">
<head>
<meta charset="utf-8">
<title>Valto Brindex AS – Business Card</title>
<link href="https://fonts.googleapis.com/css2?family=Lato:wght@300;400;700&display=swap" rel="stylesheet">
<style>
  :root {
    --backdrop: #d9dadc;
    --card: #ffffff;
    --ink: #2a2a2a;
    --ink-soft: #4a4a4a;
    --accent: #5b8fc2;
    --band: #2b2c2e;
    --band-text: #f2f2f2;
    --pattern-a: #f1f2f3;
    --pattern-b: #f8f8f9;
  }
  html, body {
    margin: 0;
    width: 1200px;
    height: 900px;
    overflow: hidden;
    background: var(--backdrop);
    font-family: "Lato", Arial, sans-serif;
  }
  .canvas {
    position: relative;
    width: 1200px;
    height: 900px;
    display: flex;
    align-items: center;
    justify-content: center;
  }
  .business-card {
    position: relative;
    width: 910px;
    height: 520px;
    background: var(--card);
    box-shadow: 0 10px 30px rgba(0,0,0,0.18);
    overflow: hidden;
    color: var(--ink);
  }
  .texture-area {
    position: absolute;
    left: 0;
    top: 110px;
    width: 560px;
    height: 208px;
    background: linear-gradient(100deg, var(--pattern-a), var(--pattern-b) 70%, var(--card));
  }
  .brand {
    position: absolute;
    left: 330px;
    top: 64px;
    display: flex;
    align-items: center;
    gap: 22px;
  }
  .brand-square {
    width: 58px;
    height: 58px;
    background: var(--accent);
  }
  .brand-name {
    font-size: 54px;
    font-weight: 400;
    letter-spacing: 2px;
    color: var(--ink-soft);
  }
  .divider {
    position: absolute;
    left: 28px;
    right: 28px;
    top: 318px;
    height: 2px;
    background: var(--accent);
  }
  .holder {
    position: absolute;
    left: 60px;
    top: 248px;
  }
  .holder-name {
    font-size: 30px;
    font-weight: 400;
    line-height: 36px;
    color: var(--accent);
    margin: 0;
  }
  .holder-title {
    font-size: 17px;
    line-height: 22px;
    letter-spacing: 1px;
    color: var(--ink);
    margin: 2px 0 0;
  }
  .contact-list {
    position: absolute;
    left: 60px;
    top: 340px;
    margin: 0;
    padding: 0;
    list-style: none;
    font-size: 21px;
    font-weight: 300;
    line-height: 33px;
  }
  .contact-list li {
    display: flex;
    align-items: center;
    gap: 14px;
  }
  .contact-icon {
    width: 18px;
    height: 18px;
    fill: none;
    stroke: var(--ink-soft);
    stroke-width: 1.6;
  }
  .company {
    position: absolute;
    right: 70px;
    top: 332px;
    text-align: right;
    font-size: 21px;
    line-height: 28px;
    font-weight: 400;
    font-style: normal;
  }
  .company-name { font-weight: 700; }
  .footer-shape {
    position: absolute;
    left: 0;
    bottom: 0;
    width: 910px;
    height: 90px;
  }
  .web-address {
    position: absolute;
    right: 50px;
    bottom: 28px;
    font-size: 22px;
    letter-spacing: 3px;
    font-weight: 400;
    color: var(--band-text);
  }
</style>
</head>
<body>
<main class="canvas">
  <article class="business-card">
    <div class="texture-area" role="img" aria-label="Faint light grey geometric block pattern"></div>

    <header class="brand">
      <span class="brand-square"></span>
      <span class="brand-name">Valto Brindex</span>
    </header>

    <div class="holder">
      <p class="holder-name">Eirik Holmvik</p>
      <p class="holder-title">DIRECTOR</p>
    </div>

    <div class="divider"></div>

    <ul class="contact-list">
      <li>
        <svg class="contact-icon" viewBox="0 0 20 20"><path d="M4 2 L8 6 L6 8 Q8 12 12 14 L14 12 L18 16 L15 19 Q6 17 1 5 Z"/></svg>
        482 71 519
      </li>
      <li>
        <svg class="contact-icon" viewBox="0 0 20 20"><rect x="5" y="2" width="10" height="6"/><rect x="2" y="8" width="16" height="7"/><rect x="5" y="13" width="10" height="5"/></svg>
        482 71 520
      </li>
      <li>
        <svg class="contact-icon" viewBox="0 0 20 20"><rect x="2" y="4" width="16" height="12"/><path d="M2 4 L10 11 L18 4"/></svg>
        eholmvik@brindex.no
      </li>
    </ul>

    <address class="company">
      <div class="company-name">Valto Brindex AS</div>
      <div>Kvernlia 14</div>
      <div>3170 Sem</div>
    </address>

    <svg class="footer-shape" viewBox="0 0 910 90" preserveAspectRatio="none" aria-hidden="true">
      <rect x="0" y="70" width="910" height="20" fill="var(--band)"/>
      <rect x="0" y="62" width="600" height="8" fill="var(--accent)"/>
      <path d="M560 0 L910 0 L910 90 L560 90 L560 70 L590 62 L600 40 Z" fill="var(--band)"/>
    </svg>
    <div class="web-address">www.brindex.no</div>
  </article>
</main>
</body>
</html>
```